Business Card for Coastal Tundrabridge Advisory

We need a business card for Coastal Tundrabridge Advisory. The company website address is provided below. The company logo is attached. We provide specialized permafrost services to the mining, transportation, and oil & gas industries. The card should be prepared for:
Matthias Korhonen, PhD.
Coastal Tundrabridge Advisory
PO Box 418259
Quillwater, Alaska 99642
Direct: +1-907-555-0143
Email: mkorhonen@tundrabridgeadvisory.example
Website: www.coastaltundrabridgeadvisory.example

```html
<!DOCTYPE html>
<html lang="en">
<head>
<meta charset="utf-8">
<title>Coastal Tundrabridge Advisory — Business Card</title>
<link href="https://fonts.googleapis.com/css2?family=Open+Sans:wght@400;600;700&display=swap" rel="stylesheet">
<style>
  :root {
    --navy: #111822;
    --paper: #ffffff;
    --ink: #111822;
    --muted: #2a2f38;
    --stage: #e9e7e3;
  }
  * { box-sizing: border-box; margin: 0; padding: 0; }
  html, body { width: 1200px; height: 780px; overflow: hidden; }
  body {
    background: var(--stage);
    font-family: "Open Sans", sans-serif;
    color: var(--ink);
    position: relative;
  }
  .card {
    position: absolute;
    top: 235px;
    width: 540px;
    height: 310px;
    overflow: hidden;
    box-shadow: 0 6px 18px rgba(0,0,0,.18);
  }

  /* Front */
  .card-front { left: 40px; background: var(--paper); }
  .front-band-left {
    position: absolute; left: 0; top: 48px;
    width: 12px; height: 118px; background: var(--navy);
  }
  .front-band-right {
    position: absolute; right: 0; bottom: 18px;
    width: 12px; height: 130px; background: var(--navy);
  }
  .front-logo {
    position: absolute; left: 34px; top: 60px; width: 200px;
    font-weight: 700; font-size: 21px; line-height: 1.12;
    letter-spacing: .5px; text-transform: uppercase; color: var(--ink);
  }
  .divider {
    position: absolute; left: 0; top: 0; width: 540px; height: 310px;
  }
  .person { position: absolute; left: 262px; top: 108px; }
  .person-name { font-size: 25px; line-height: 1.1; white-space: nowrap; }
  .person-name .first { font-weight: 700; }
  .person-name .last { font-weight: 400; }
  .person-title { font-weight: 700; font-size: 15px; margin-top: 1px; }
  .contacts { list-style: none; margin-top: 12px; }
  .contacts li {
    display: flex; align-items: center; gap: 7px;
    font-size: 11.5px; line-height: 1.55; white-space: nowrap; color: var(--muted);
  }
  .contacts svg { width: 11px; height: 11px; flex: none; }
  .address {
    position: absolute; left: 34px; bottom: 36px;
    font-size: 12px; line-height: 1.5; color: var(--muted);
  }

  /* Back */
  .card-back { right: 40px; background: var(--navy); color: var(--paper); }
  .back-logo {
    position: absolute; left: 60px; right: 40px; top: 78px;
    font-weight: 700; font-size: 30px; line-height: 1.1;
    letter-spacing: 1px; text-transform: uppercase; color: var(--paper);
    text-align: center;
  }
  .services {
    position: absolute; left: 0; right: 0; bottom: 46px; text-align: center;
  }
  .services-heading { font-weight: 700; font-size: 11px; letter-spacing: .3px; }
  .services-text { font-size: 11px; margin-top: 4px; padding: 0 24px; }
</style>
</head>
<body>

  <section class="card card-front" aria-label="Business card front">
    <div class="front-band-left"></div>
    <div class="front-band-right"></div>
    <div class="front-logo">Coastal Tundrabridge Advisory</div>
    <svg class="divider" viewBox="0 0 540 310" aria-hidden="true">
      <line x1="252" y1="92" x2="200" y2="232" stroke="#111822" stroke-width="1"/>
    </svg>
    <div class="person">
      <h1 class="person-name"><span class="first">Matthias</span> <span class="last">Korhonen</span></h1>
      <p class="person-title">PhD</p>
      <ul class="contacts">
        <li>
          <svg viewBox="0 0 24 24" aria-hidden="true"><path fill="#111822" d="M6.6 10.8a15 15 0 0 0 6.6 6.6l2.2-2.2a1 1 0 0 1 1-.25 11.4 11.4 0 0 0 3.6.57 1 1 0 0 1 1 1V20a1 1 0 0 1-1 1A17 17 0 0 1 3 4a1 1 0 0 1 1-1h3.5a1 1 0 0 1 1 1c0 1.25.2 2.45.57 3.6a1 1 0 0 1-.25 1z"/></svg>
          +1-907-555-0143
        </li>
        <li>
          <svg viewBox="0 0 24 24" aria-hidden="true"><circle cx="12" cy="12" r="11" fill="#111822"/><circle cx="12" cy="12" r="3.6" fill="none" stroke="#fff" stroke-width="1.8"/><path d="M15.6 9v4.2a2 2 0 0 0 3.6 1.2A7.5 7.5 0 1 0 16 18" fill="none" stroke="#fff" stroke-width="1.8"/></svg>
          mkorhonen@tundrabridgeadvisory.example
        </li>
        <li>
          <svg viewBox="0 0 24 24" aria-hidden="true"><circle cx="12" cy="12" r="11" fill="#111822"/><ellipse cx="12" cy="12" rx="4.5" ry="10" fill="none" stroke="#fff" stroke-width="1.3"/><line x1="2" y1="12" x2="22" y2="12" stroke="#fff" stroke-width="1.3"/></svg>
          www.coastaltundrabridgeadvisory.example
        </li>
      </ul>
    </div>
    <p class="address">PO Box 418259<br>Quillwater, Alaska 99642</p>
  </section>

  <section class="card card-back" aria-label="Business card back">
    <div class="back-logo">Coastal Tundrabridge Advisory</div>
    <div class="services">
      <p class="services-heading">OUR SERVICES</p>
      <p class="services-text">We provide specialized permafrost services to the mining, transportation, and oil &amp; gas industries</p>
    </div>
  </section>

</body>
</html>
```